Craft Brewery needs a banner design for a festival

We need a Large banner design for the Feast at Wyndale festival.We would like to see a lot of natural rainforest theme with small creeks and rivers as our name is Copper Hollow Brewing co.

We need this to look attractive to our brand of naturally brewed beers.

Banner dimension are
3000mm Width
1150mm Height
Updates

Hey guys thanks for the designs, i have added a couple of more pics for inspiration one with ferns which we would like in the design and the other named dramvolt which i like the background with all the brewing pics. Cheers Dave

Target Market(s)

Beer drinkers

Colors

Designer to choose colors to be used in the design.

Requirements
Must have
• Rainforest, Streams and rivers, nature, Logo
• The ingredients
Nice to have
• na
Should not have
• Na

```html
<!DOCTYPE html>
<html lang="en">
<head>
<meta charset="utf-8">
<title>Copper Hollow Brewing co – Festival Banner</title>
<link rel="stylesheet" href="https://fonts.googleapis.com/css2?family=Kaushan+Script&family=Jost:wght@400;600&display=swap">
<style>
  :root {
    --moss-deep: #2f4214;
    --moss: #5e7a22;
    --fern: #9cbc3a;
    --grass-gold: #b9b048;
    --stone: #6a6555;
    --stone-dark: #3a3a30;
    --water-foam: #eef4f8;
    --water: #9dbad0;
    --water-deep: #2f4a5c;
    --ink: #2e3a1c;
    --white: #ffffff;
  }
  html, body {
    margin: 0;
    padding: 0;
    overflow: hidden;
    background: #ffffff;
  }
  .banner {
    position: relative;
    width: 1200px;
    height: 460px;
    overflow: hidden;
    font-family: "Jost", sans-serif;
  }
  .creek-scene {
    position: absolute;
    inset: 0;
    background:
      radial-gradient(ellipse 180px 60px at 430px 400px, rgba(238,244,248,0.95) 0%, rgba(238,244,248,0) 100%),
      radial-gradient(ellipse 120px 180px at 380px 120px, rgba(238,244,248,0.9) 0%, rgba(238,244,248,0) 100%),
      radial-gradient(ellipse 160px 110px at 560px 230px, rgba(157,186,208,0.9) 0%, rgba(157,186,208,0) 100%),
      radial-gradient(ellipse 200px 80px at 430px 330px, rgba(47,74,92,0.85) 0%, rgba(47,74,92,0) 100%),
      radial-gradient(ellipse 110px 70px at 700px 70px, rgba(106,101,85,0.9) 0%, rgba(106,101,85,0) 100%),
      radial-gradient(ellipse 140px 90px at 680px 360px, rgba(94,122,34,0.9) 0%, rgba(94,122,34,0) 100%),
      radial-gradient(ellipse 200px 160px at 1110px 120px, rgba(156,188,58,0.95) 0%, rgba(156,188,58,0) 100%),
      radial-gradient(ellipse 240px 160px at 1050px 400px, rgba(94,122,34,0.95) 0%, rgba(94,122,34,0) 100%),
      radial-gradient(ellipse 140px 200px at 40px 130px, rgba(185,176,72,0.85) 0%, rgba(185,176,72,0) 100%),
      radial-gradient(ellipse 220px 110px at 120px 400px, rgba(47,66,20,0.95) 0%, rgba(47,66,20,0) 100%),
      linear-gradient(90deg,
        var(--moss-deep) 0%,
        var(--stone) 18%,
        var(--water) 30%,
        var(--water-foam) 38%,
        var(--water) 46%,
        var(--stone-dark) 56%,
        var(--moss) 66%,
        var(--moss) 80%,
        var(--fern) 92%,
        var(--moss-deep) 100%);
  }
  .brand-mark {
    position: absolute;
    left: 76px;
    top: 80px;
    width: 232px;
    height: 232px;
    border-radius: 50%;
    background: var(--white);
    display: flex;
    align-items: center;
    justify-content: center;
    text-align: center;
  }
  .brand-name {
    margin: 0;
    font-weight: 600;
    font-size: 28px;
    line-height: 1.1;
    color: var(--ink);
  }
  .headline {
    margin: 0;
    font-family: "Kaushan Script", cursive;
    font-weight: 400;
    color: var(--white);
    text-shadow: 0 2px 6px rgba(0,0,0,0.45);
  }
  .headline span {
    position: absolute;
    line-height: 1;
    white-space: nowrap;
  }
  .headline-top {
    left: 718px;
    top: 70px;
    font-size: 66px;
  }
  .headline-in {
    left: 770px;
    top: 160px;
    font-size: 46px;
  }
  .headline-place {
    left: 822px;
    top: 150px;
    font-size: 92px;
  }
  .ingredients {
    position: absolute;
    left: 840px;
    top: 254px;
    width: 300px;
    margin: 0;
    text-align: center;
    font-family: "Kaushan Script", cursive;
    font-size: 27px;
    line-height: 1.25;
    color: var(--white);
    text-shadow: 0 2px 4px rgba(0,0,0,0.5);
  }
</style>
</head>
<body>
  <div class="banner">
    <div class="creek-scene" role="img" aria-label="Photograph of a mossy rainforest creek with small waterfalls cascading over rocks, ferns and grasses along the banks"></div>

    <div class="brand-mark">
      <p class="brand-name">Copper Hollow<br>Brewing co</p>
    </div>

    <h1 class="headline">
      <span class="headline-top">Handcrafted</span>
      <span class="headline-in">in</span>
      <span class="headline-place">Tasmania</span>
    </h1>

    <p class="ingredients">Water, hops, malt, yeast<br>and nothing else</p>
  </div>
</body>
</html>
```